Medical Billing Company Needs a Business Card Design

We need a business card design for a Florida based medical billing company called 'Clinicians Keystone Solutions'. We specialize in providing revenue cycle management services to physician and therapist offices (we're basically their back-office processing partner for providing billing software, claims submissions, A/R follow-up and patient statements & collections. Our logo is red and blue-ish, so make sure that whatever other elements are used will match appropriately. Our current business card design has a too small font size. I'd like to project an image that shows we are modern & reliable. On a side note, I'm planning on using ZUB for printing these cards.

Target Market(s)

Office managers, physicians, therapists

Industry/Entity Type

Printing

Requirements
Must have
• Logo
Name of Employee
Phone
Fax
E-mail
Website

```html
<!DOCTYPE html>
<html lang="en">
<head>
<meta charset="utf-8">
<title>Clinicians Keystone Solutions – Business Card</title>
<link href="https://fonts.googleapis.com/css2?family=Source+Sans+3:wght@400;600;700&display=swap" rel="stylesheet">
<style>
  :root {
    --navy: #2a1c7a;
    --navy-deep: #1c0e66;
    --violet: #4b3a9c;
    --crimson: #a8182a;
    --ink: #2b2b33;
    --grey: #55555c;
    --paper: #ffffff;
    --backdrop: #e6e6ea;
  }
  * { margin: 0; padding: 0; box-sizing: border-box; }
  html, body { width: 1200px; height: 987px; overflow: hidden; }
  body {
    background: var(--backdrop);
    font-family: "Source Sans 3", "Segoe UI", sans-serif;
    position: relative;
  }
  .card {
    position: absolute;
    width: 620px;
    height: 354px;
    background: var(--paper);
    border-radius: 26px;
    overflow: hidden;
    box-shadow: 0 6px 18px rgba(0,0,0,0.14);
  }
  .card--back { left: 520px; top: 110px; }
  .card--front { left: 70px; top: 520px; }

  .wordmark {
    position: absolute;
    color: var(--navy);
    font-weight: 600;
    letter-spacing: 0.06em;
    text-transform: uppercase;
    white-space: nowrap;
    display: flex;
    align-items: center;
    gap: 12px;
  }
  .wordmark__square {
    width: 20px; height: 20px;
    background: var(--crimson);
    display: inline-block;
  }
  .card--back .wordmark { left: 0; right: 0; justify-content: center; top: 130px; font-size: 30px; }
  .card--back .website {
    position: absolute; left: 0; right: 0; top: 192px;
    text-align: center; font-size: 19px; letter-spacing: 0.28em; color: var(--grey);
  }
  .website .first { color: var(--violet); }
  .website .second { color: var(--crimson); }

  .card--front .wordmark { left: 150px; top: 36px; font-size: 24px; }
  .person {
    position: absolute; left: 300px; top: 94px; font-size: 26px;
  }
  .person__name { color: var(--violet); font-weight: 700; }
  .person__title { color: var(--crimson); font-weight: 400; }

  .contacts {
    position: absolute; left: 230px; top: 148px;
    font-size: 18px; color: var(--ink); line-height: 1.55;
  }
  .contacts__row { display: flex; align-items: center; gap: 6px; }
  .contacts__row .gap { width: 14px; }
  .icon { width: 15px; height: 15px; flex: none; }

  .band { position: absolute; inset: 0; width: 620px; height: 354px; }
  .address {
    position: absolute; left: 26px; bottom: 22px;
    color: #fff; font-size: 17px; letter-spacing: 0.02em;
  }
</style>
</head>
<body>

<section class="card card--back">
  <div class="wordmark"><span class="wordmark__square"></span>Clinicians Keystone Solutions</div>
  <p class="website">www.<span class="first">clinicians</span><span class="second">keystone</span>.com</p>
</section>

<section class="card card--front">
  <svg class="band" viewBox="0 0 620 354" aria-hidden="true">
    <defs>
      <linearGradient id="bandFill" x1="0" y1="0" x2="1" y2="1">
        <stop offset="0" stop-color="#4b3a9c"/>
        <stop offset="1" stop-color="#1c0e66"/>
      </linearGradient>
    </defs>
    <path d="M0 168 C150 238 330 318 580 354 L0 354 Z" fill="url(#bandFill)"/>
    <path d="M0 150 C160 226 340 306 600 350" fill="none" stroke="#a8182a" stroke-width="3"/>
  </svg>

  <div class="wordmark"><span class="wordmark__square"></span>Clinicians Keystone Solutions</div>

  <p class="person"><span class="person__name">Your Name,</span> <span class="person__title">Title</span></p>

  <div class="contacts">
    <p class="contacts__row">
      <svg class="icon" viewBox="0 0 16 16" aria-hidden="true"><rect x="1" y="3" width="14" height="10" rx="1.5" fill="var(--navy)"/><path d="M1.5 4 L8 9 L14.5 4" stroke="#fff" stroke-width="1.4" fill="none"/></svg>
      info@clinicianskeystone.com
    </p>
    <p class="contacts__row">
      <svg class="icon" viewBox="0 0 16 16" aria-hidden="true"><circle cx="8" cy="8" r="7.2" fill="none" stroke="var(--navy)" stroke-width="1.4"/><path d="M5.5 4.5 L7 4.5 L7.6 6.6 L6.7 7.4 C7.2 8.6 7.9 9.3 9 9.8 L9.8 8.9 L11.7 9.5 L11.7 11 C8 11.4 5 8.4 5.5 4.5 Z" fill="var(--navy)"/></svg>
      123-456-0789
      <span class="gap"></span>
      <svg class="icon" viewBox="0 0 16 16" aria-hidden="true"><rect x="4" y="1" width="8" height="14" rx="1.5" fill="var(--navy)"/><rect x="5.3" y="2.8" width="5.4" height="7.5" fill="#fff"/><circle cx="8" cy="12.6" r="0.9" fill="#fff"/></svg>
      123-456-0789
    </p>
    <p class="contacts__row">
      <svg class="icon" viewBox="0 0 16 16" aria-hidden="true"><circle cx="8" cy="8" r="7" fill="none" stroke="var(--navy)" stroke-width="1.3"/><ellipse cx="8" cy="8" rx="3" ry="7" fill="none" stroke="var(--navy)" stroke-width="1.1"/><path d="M1 8 H15 M2.2 4.5 H13.8 M2.2 11.5 H13.8" stroke="var(--navy)" stroke-width="1.1"/></svg>
      www.clinicianskeystone.com
    </p>
  </div>

  <p class="address">Street Name, City Name, State Zip Code</p>
</section>

</body>
</html>
```